Quote Cards With KB May 2025 for Instagram

I would like to put these quotes over one of the pictures attached; Instagram (new size: 4:5 (1080 x 1350 pixels) One Quote per picture, and I want the quote to be bold or easy to read as well. I provided a few reference graphics that I really like as examples below. In very small letters at the bottom add @KBHarlowOnline

All of the pictures are attached; you can pick any photo and add one quote to it; but no stock photography

```html
<!DOCTYPE html>
<html lang="en">
<head>
<meta charset="utf-8">
<title>Quote Cards – KB – May 2025</title>
<link rel="stylesheet" href="https://fonts.googleapis.com/css2?family=Oswald:wght@500&family=Roboto:wght@500&display=swap">
<style>
  :root {
    --canvas-bg: #dcdcdc;
    --band: #d8006c;
    --text-light: #ffffff;
    --card-w: 437px;
    --card-h: 547px;
    --photo-w: 193px;
    --band-top: 482px;
    --band-h: 29px;
  }
  * { box-sizing: border-box; margin: 0; padding: 0; }
  html, body {
    width: 1200px;
    height: 2957px;
    overflow: hidden;
    background: var(--canvas-bg);
  }
  .board {
    position: relative;
    width: 1200px;
    height: 2957px;
    padding: 87px 0 0 154px;
    display: grid;
    grid-template-columns: repeat(2, var(--card-w));
    grid-auto-rows: var(--card-h);
    column-gap: 17px;
    row-gap: 12px;
  }
  .quote-card {
    position: relative;
    width: var(--card-w);
    height: var(--card-h);
    overflow: hidden;
  }
  .quote-card__photo {
    position: absolute;
    inset: 0;
    background: var(--photo-bg);
  }
  .quote-card__panel {
    position: absolute;
    top: 0;
    left: var(--photo-w);
    right: 0;
    height: var(--band-top);
    background: var(--panel-bg);
    padding: var(--text-top, 56px) 2px 0;
    display: flex;
    justify-content: center;
  }
  .quote-card__text {
    font-family: "Oswald", sans-serif;
    font-weight: 500;
    font-size: var(--text-size, 39px);
    line-height: var(--text-lh, 43.7px);
    letter-spacing: -1px;
    white-space: nowrap;
    color: var(--text-light);
    text-align: center;
    text-shadow: 0 2px 3px rgba(60, 0, 30, 0.55);
  }
  .quote-card__band {
    position: absolute;
    left: 0;
    right: 0;
    top: var(--band-top);
    height: var(--band-h);
    background: var(--band);
    display: flex;
    align-items: center;
    justify-content: center;
    font-family: "Roboto", sans-serif;
    font-weight: 500;
    font-size: 11px;
    color: var(--text-light);
  }

  .card-1 { --photo-bg: linear-gradient(180deg, #9cc9e6 0%, #5e6b5a 45%, #2a2a2a 80%, #3c3a30 100%); --panel-bg: rgba(214, 88, 160, 0.93); --text-top: 58px; --text-lh: 43.7px; --text-size: 39px; }
  .card-2 { --photo-bg: linear-gradient(180deg, #4a3a30 0%, #2c2220 50%, #1a1616 100%); --panel-bg: rgba(160, 18, 80, 0.95); --text-top: 58px; --text-lh: 43.7px; --text-size: 39px; }
  .card-3 { --photo-bg: linear-gradient(180deg, #7fa6b8 0%, #b06e8a 45%, #d89a3a 80%, #6a8a9a 100%); --panel-bg: rgba(176, 40, 110, 0.88); --text-top: 46px; --text-lh: 41.3px; --text-size: 37px; }
  .card-4 { --photo-bg: linear-gradient(180deg, #2a3040 0%, #8a6a4a 50%, #c89a5a 85%, #e0b020 100%); --panel-bg: rgba(178, 22, 70, 0.92); --text-top: 58px; --text-lh: 43.5px; --text-size: 39px; }
  .card-5 { --photo-bg: linear-gradient(180deg, #c8c4c0 0%, #e6e2de 40%, #2a2226 80%, #5a5050 100%); --panel-bg: rgba(170, 70, 140, 0.9); --text-top: 47px; --text-lh: 41.3px; --text-size: 37px; }
  .card-6 { --photo-bg: linear-gradient(180deg, #3a2a6a 0%, #7a3a9a 40%, #d02a90 75%, #e040a0 100%); --panel-bg: rgba(150, 24, 110, 0.9); --text-top: 56px; --text-lh: 44px; --text-size: 39px; }
  .card-7 { --photo-bg: linear-gradient(180deg, #5a5a6a 0%, #8a5070 45%, #2a2228 80%, #3a3438 100%); --panel-bg: rgba(136, 22, 94, 0.93); --text-top: 47px; --text-lh: 41.2px; --text-size: 37px; }
  .card-8 { --photo-bg: linear-gradient(180deg, #2a2428 0%, #1c1a1e 50%, #5a3a6a 85%, #2a2228 100%); --panel-bg: rgba(168, 52, 130, 0.9); --text-top: 56px; --text-lh: 43.7px; --text-size: 39px; }
  .card-9 { --photo-bg: linear-gradient(180deg, #9aa8a0 0%, #6a7a60 40%, #222022 75%, #2a2a2a 100%); --panel-bg: rgba(184, 70, 142, 0.92); --text-top: 48px; --text-lh: 39px; --text-size: 35px; }
  .card-10 { --photo-bg: linear-gradient(180deg, #d8d4d0 0%, #b8b0ac 40%, #3a3034 80%, #2a2226 100%); --panel-bg: rgba(192, 72, 146, 0.93); --text-top: 56px; --text-lh: 43.7px; --text-size: 39px; }
</style>
</head>
<body>
<main class="board">

  <article class="quote-card card-1">
    <div class="quote-card__photo" role="img" aria-label="Photo of KB in a black outfit outdoors with hills behind"></div>
    <div class="quote-card__panel"><p class="quote-card__text">Tired. Moody.<br>Stubborn Belly<br>Fat. Your<br>hormones<br>are screaming<br>for help!<br>Let’s fix that.</p></div>
    <div class="quote-card__band">@KBHarlowOnline</div>
  </article>

  <article class="quote-card card-2">
    <div class="quote-card__photo" role="img" aria-label="Photo of KB in a sheer striped black top in a kitchen"></div>
    <div class="quote-card__panel"><p class="quote-card__text">That stubborn<br>weight? It’s not<br>your fault.<br>Your hormones<br>are to blame<br>and you’re not<br>alone; But there<br>is a fix.</p></div>
    <div class="quote-card__band">@KBHarlowOnline</div>
  </article>

  <article class="quote-card card-3">
    <div class="quote-card__photo" role="img" aria-label="Photo of KB in a pink outfit beside sunflowers and neon lights"></div>
    <div class="quote-card__panel"><p class="quote-card__text">Your belly<br>isn’t fat… it’s<br>hormonal.<br>And here’s how<br>to fix it.<br>Comment<br>HORMONES if<br>nothing is<br>working.</p></div>
    <div class="quote-card__band">@KBHarlowOnline</div>
  </article>

  <article class="quote-card card-4">
    <div class="quote-card__photo" role="img" aria-label="Photo of KB standing on a basketball court in a sparkly bodysuit"></div>
    <div class="quote-card__panel"><p class="quote-card__text">The stubborn<br>belly fat after<br>40? It’s not<br>about calories;<br>it’s about your<br>hormones.<br>Here is the<br>fix!</p></div>
    <div class="quote-card__band">@KBHarlowOnline</div>
  </article>

  <article class="quote-card card-5">
    <div class="quote-card__photo" role="img" aria-label="Photo of KB in a white crop top pointing upward"></div>
    <div class="quote-card__panel"><p class="quote-card__text">Flat tummy<br>in your<br>40s? It’s still<br>possible!<br>Comment<br>BYE BELLY<br>to get the 10<br>secrets to a<br>flatter tummy</p></div>
    <div class="quote-card__band">@KBHarlowOnline</div>
  </article>

  <article class="quote-card card-6">
    <div class="quote-card__photo" role="img" aria-label="Photo of KB in a pink gown on a purple lit stage"></div>
    <div class="quote-card__panel"><p class="quote-card__text">Bloating.<br>Muffin top.<br>Puffy waistline.<br>Your body’s<br>screaming<br>for a different<br>kind of fix.<br>Here it is</p></div>
    <div class="quote-card__band">@KBHarlowOnline</div>
  </article>

  <article class="quote-card card-7">
    <div class="quote-card__photo" role="img" aria-label="Photo of KB courtside holding a basketball"></div>
    <div class="quote-card__panel"><p class="quote-card__text">You’re doing<br>all the “right”<br>things, but your<br>belly won’t<br>go down?<br>Here’s what<br>you haven’t<br>tried.</p></div>
    <div class="quote-card__band">@KBHarlowOnline</div>
  </article>

  <article class="quote-card card-8">
    <div class="quote-card__photo" role="img" aria-label="Photo of KB in a sheer black top with a city view at night"></div>
    <div class="quote-card__panel"><p class="quote-card__text">This 90-day<br>plan helped<br>women over<br>40 slim down,<br>get a tiny waist<br>and feel sexy<br>again.<br>You’re next.</p></div>
    <div class="quote-card__band">@KBHarlowOnline</div>
  </article>

  <article class="quote-card card-9">
    <div class="quote-card__photo" role="img" aria-label="Photo of KB in a black top and jeans outdoors"></div>
    <div class="quote-card__panel"><p class="quote-card__text">This is the<br>secret women<br>over 40 are<br>using to get<br>snatched;<br>without starving.<br>Comment SKINNY<br>to get the<br>exact plan.</p></div>
    <div class="quote-card__band">@KBHarlowOnline</div>
  </article>

  <article class="quote-card card-10">
    <div class="quote-card__photo" role="img" aria-label="Photo of KB in a sheer striped black top against a light wall"></div>
    <div class="quote-card__panel"><p class="quote-card__text">What worked<br>in your 30s<br>won’t work<br>now. Here’s<br>what actually<br>does. Drop 30<br>Pounds in<br>3 Months.</p></div>
    <div class="quote-card__band">@KBHarlowOnline</div>
  </article>

</main>
</body>
</html>
```